UI Improvement for FlorKeep app

We are looking for a talented UI/UX designer to REFINE and enhance the visual design of our mobile application, FlorKeep. The app is fully functional, but we need a designer to improve its aesthetics by specifying design elements such as fonts, colors, spacing, and component styles.
Your task will be to analyze the CURRENT UI and provide detailed design specifications that will make the app more visually appealing, modern, and user-friendly.
TODO:
Review the existing FlorKeep app design (see attachments) and identify areas for visual improvement.
Provide a detailed UI style guide, including:
Typography (font choices, sizes, and weights)
Color palette (primary, secondary, and accent colors)
Component styling (buttons, forms, icons, and interactive elements)
Spacing and layout guidelines (margins, paddings, and alignment)
Ensure the design remains clean, modern, and professional while maintaining usability and accessibility.
Provide design mockups or visual examples (if possible) to illustrate the proposed changes.
Deliverables:
A UI Style Guide (PDF or Figma file) with specifications on fonts, colors, spacing, and UI components.
Optionally, before/after mockups or examples demonstrating the improvements.
Ideal Designer:
Strong experience in mobile UI/UX design.
Understanding of modern design trends and best practices.
Ability to communicate design choices clearly for easy developer implementation.
I have attached 7 images showcasing the main UI screens used in the FlorKeep app. These screens need visual enhancements to improve their overall look and user experience.
The images represent the current design in three key modes:
LIST Mode – Displays data in a structured list format.
READ Mode – Shows detailed information when a user selects an item.
ADD/EDIT Mode – Allows users to input or modify information.
Additionally, there is a ‘MORE’ page, which serves as a menu listing other features of the application.
Task Objective:
Please refine and improve these UIs to create a more modern, visually appealing, and user-friendly experience. Focus on typography, colors, spacing, and component styling to ensure a cohesive and polished design.
Look and feel
Each slider illustrates characteristics of the customer's brand and the style your logo design should communicate.

```html
<!DOCTYPE html>
<html lang="en">
<head>
<meta charset="utf-8">
<title>FlorKeep – UI Screens</title>
<link rel="stylesheet" href="https://fonts.googleapis.com/css2?family=Nunito+Sans:wght@400;600;700;800&display=swap">
<style>
:root{
  --bg:#808285;
  --blue:#1c4f9c;
  --blue-text:#1d4f9e;
  --green:#1ba47b;
  --white:#ffffff;
  --ink:#1d1d1f;
  --soft-blue:#e4f1fb;
  --chip-blue:#dceafa;
  --line:#d9dde3;
  --card-shadow:0 1px 3px rgba(0,0,0,.12);
}
*{box-sizing:border-box;margin:0;padding:0}
html,body{width:1200px;height:429px;overflow:hidden}
body{background:var(--bg);font-family:"Nunito Sans",Arial,sans-serif;color:var(--ink);position:relative}
svg{display:block}
.screen{position:absolute;background:var(--white);overflow:hidden}
.screen--phone{left:47px;top:43px;width:161px;height:349px;border-radius:16px;background:var(--white)}
.screen--pilots{left:262px;top:32px;width:208px;height:368px}
.screen--more{left:499px;top:32px;width:208px;height:368px}
.screen--contact{left:732px;top:31px;width:207px;height:368px}
.screen--workorder{left:964px;top:30px;width:208px;height:368px}

.appbar{position:absolute;left:0;top:0;right:0;height:27px;background:var(--blue);color:var(--white);display:flex;align-items:center;padding:0 9px;gap:6px}
.appbar__title{font-weight:800;font-size:10px;letter-spacing:.2px;flex:1}
.appbar__icon{width:12px;height:12px;color:var(--white)}
.appbar__kebab{width:4px;height:12px}
.screen--phone .appbar{height:44px;align-items:flex-end;padding:0 4px 10px}
.screen--phone .appbar__title{font-size:8px}
.screen--phone .appbar__icon{width:10px;height:10px}

/* menu grid */
.menu{position:absolute;display:grid;grid-template-columns:repeat(3,1fr)}
.menu__cell{background:var(--white);box-shadow:var(--card-shadow);border-radius:2px;display:flex;flex-direction:column;align-items:center;justify-content:center;text-align:center;color:var(--ink);font-weight:600;line-height:1.15}
.menu__cell svg{color:var(--blue)}
.menu__wide{position:absolute;background:var(--white);box-shadow:var(--card-shadow);display:flex;align-items:center;justify-content:center;gap:8px;font-weight:600}
.menu__wide svg{color:var(--blue)}
.screen--phone .menu{left:4px;top:54px;width:154px;grid-template-rows:repeat(3,45px);gap:6px}
.screen--phone .menu__cell{font-size:5px;gap:6px}
.screen--phone .menu__cell svg{width:13px;height:13px}
.screen--phone .menu__wide{left:4px;top:209px;width:154px;height:26px;font-size:5px}
.screen--phone .menu__wide svg{width:13px;height:13px}
.screen--more .menu{left:10px;top:38px;width:186px;grid-template-rows:repeat(3,55px);gap:5px 8px}
.screen--more .menu__cell{font-size:6.4px;gap:8px}
.screen--more .menu__cell svg{width:17px;height:17px}
.screen--more .menu__wide{left:10px;top:224px;width:186px;height:32px;font-size:6.4px}
.screen--more .menu__wide svg{width:17px;height:17px}

/* bottom nav */
.tabbar{position:absolute;left:0;right:0;bottom:0;height:31px;background:var(--blue);display:flex}
.tabbar__item{flex:1;display:flex;flex-direction:column;align-items:center;justify-content:center;gap:3px;color:var(--white);font-size:5.6px;font-weight:600;white-space:nowrap}
.tabbar__item svg{width:10px;height:10px}
.tabbar__item--active{background:var(--green)}
.tabbar__item--wide{flex:1.35}
.screen--phone .tabbar{bottom:22px;height:26px}
.screen--phone .tabbar__item{font-size:4.6px;gap:2px}
.screen--phone .tabbar__item svg{width:8px;height:8px}
.screen--phone .phone-foot{position:absolute;left:0;right:0;bottom:0;height:22px;background:var(--blue)}

/* pilots */
.search{position:absolute;left:8px;top:36px;width:194px;height:24px;border:1.3px solid var(--blue);border-radius:12px;display:flex;align-items:center;gap:5px;padding-left:10px;color:var(--blue-text);font-weight:700;font-size:7px}
.search svg{width:9px;height:9px}
.advanced{position:absolute;right:9px;top:64px;display:flex;align-items:center;gap:3px;font-size:5.6px;color:#333}
.advanced svg{width:7px;height:7px}
.pilot{position:absolute;left:8.5px;width:191px;height:57px;background:var(--white);border:1px solid #e3e7ec;border-radius:5px;box-shadow:var(--card-shadow)}
.pilot__photo{position:absolute;left:8px;top:8px;width:40px;height:40px;border-radius:50%;background:radial-gradient(circle at 50% 40%,#d9b79a 0 30%,#3b4454 55%,#c9ccd1 100%)}
.pilot__name{position:absolute;left:62px;top:11px;font-size:8px;font-weight:700;color:var(--blue-text)}
.pilot__chips{position:absolute;left:60px;top:28px;display:flex;gap:6px}
.chip{height:15px;border-radius:8px;display:flex;align-items:center;justify-content:center;font-size:6.8px;color:var(--blue-text);width:43px}
.chip--fill{background:var(--chip-blue)}
.chip--line{border:1px solid var(--blue)}

/* contact */
.addrow{position:absolute;left:7.5px;width:191px;height:18px;border:1px solid var(--blue);border-radius:9px;display:flex;align-items:center;justify-content:space-between;padding:0 5px 0 11px;font-size:5.8px;font-weight:600;color:var(--blue-text)}
.addrow svg{width:7px;height:7px;color:var(--blue)}
.panel{position:absolute;left:7.5px;width:191px;background:var(--soft-blue);border-radius:8px;padding:7px 11px;font-size:5.4px;color:#222}
.panel__title{font-weight:600;color:var(--blue-text);font-size:5.8px;margin-bottom:9px}
.panel__toggle{position:absolute;right:6px;top:6px;width:7px;height:7px;color:var(--blue)}
.panel p{line-height:1.75}
.pill-btn{display:inline-block;margin-top:8px;background:var(--green);color:var(--white);font-weight:700;font-size:4.6px;padding:3px 8px;border-radius:6px}

/* work order */
.toggle-row{position:absolute;left:7.5px;top:37px;display:flex;gap:4px}
.toggle{height:18px;border:1px solid var(--blue);border-radius:9px;display:flex;align-items:center;justify-content:center;font-size:5.8px;font-weight:600;color:var(--blue-text)}
.toggle--on{background:var(--green);border-color:var(--green);color:var(--white)}
.action-row{position:absolute;left:8px;top:62px;display:flex;gap:6px}
.action{height:18px;border-radius:9px;background:var(--white);box-shadow:var(--card-shadow);display:flex;align-items:center;justify-content:center;gap:4px;font-size:6.2px;font-weight:600;color:var(--blue-text)}
.action svg{width:7px;height:7px}
.detail{position:absolute;left:9px;top:92px;width:190px;height:189px;background:var(--white);border-radius:6px;box-shadow:var(--card-shadow);padding:7px 9px 0 12px}
.detail__toggle{position:absolute;right:7px;top:7px;width:7px;height:7px;color:var(--blue)}
.field{border-bottom:.6px solid var(--line);height:26.4px;padding-top:2px;font-size:6.8px;line-height:1.3}
.field:last-child{border-bottom:none}
.field dt{font-weight:700}
.field dd{color:#222}
</style>
</head>
<body>
<svg width="0" height="0" style="position:absolute" aria-hidden="true">
  <defs>
    <symbol id="i-plus" viewBox="0 0 24 24"><circle cx="12" cy="12" r="10" fill="none" stroke="currentColor" stroke-width="1.8"/><path d="M12 7v10M7 12h10" stroke="currentColor" stroke-width="1.8"/></symbol>
    <symbol id="i-minus" viewBox="0 0 24 24"><circle cx="12" cy="12" r="10" fill="none" stroke="currentColor" stroke-width="1.8"/><path d="M7 12h10" stroke="currentColor" stroke-width="1.8"/></symbol>
    <symbol id="i-kebab" viewBox="0 0 6 24"><circle cx="3" cy="3" r="2.4" fill="currentColor"/><circle cx="3" cy="12" r="2.4" fill="currentColor"/><circle cx="3" cy="21" r="2.4" fill="currentColor"/></symbol>
    <symbol id="i-back" viewBox="0 0 24 24"><path d="M16 3 7 12l9 9" fill="none" stroke="currentColor" stroke-width="3" stroke-linecap="round" stroke-linejoin="round"/></symbol>
    <symbol id="i-search" viewBox="0 0 24 24"><circle cx="10" cy="10" r="7" fill="none" stroke="currentColor" stroke-width="2.6"/><path d="m15 15 6 6" stroke="currentColor" stroke-width="2.6" stroke-linecap="round"/></symbol>
    <symbol id="i-cog" viewBox="0 0 24 24"><circle cx="12" cy="12" r="7" fill="none" stroke="currentColor" stroke-width="3" stroke-dasharray="3 2.5"/><circle cx="12" cy="12" r="5" fill="none" stroke="currentColor" stroke-width="1.6"/></symbol>
    <symbol id="i-gear" viewBox="0 0 24 24"><circle cx="12" cy="12" r="8" fill="none" stroke="currentColor" stroke-width="5" stroke-dasharray="4 2.3"/><circle cx="12" cy="12" r="6.5" fill="currentColor"/><circle cx="12" cy="12" r="3" fill="#fff"/></symbol>
    <symbol id="i-phone" viewBox="0 0 24 24"><path fill="currentColor" d="M6.6 10.8c1.4 2.8 3.8 5.1 6.6 6.6l2.2-2.2c.3-.3.7-.4 1-.2 1.1.4 2.3.6 3.6.6.6 0 1 .4 1 1V20c0 .6-.4 1-1 1C10.6 21 3 13.4 3 4c0-.6.4-1 1-1h3.5c.6 0 1 .4 1 1 0 1.3.2 2.5.6 3.6.1.3 0 .7-.2 1z"/></symbol>
    <symbol id="i-pilot" viewBox="0 0 24 24"><path fill="currentColor" d="M6 3h12l-1 4H7z"/><circle cx="12" cy="11" r="3.6" fill="currentColor"/><path fill="currentColor" d="M4 22c0-4.5 3.5-7 8-7s8 2.5 8 7z"/><path d="M12 15.5v6" stroke="#fff" stroke-width="1.2"/></symbol>
    <symbol id="i-plane" viewBox="0 0 24 24"><path fill="currentColor" transform="rotate(45 12 12)" d="M21 16v-2l-8-5V3.5a1.5 1.5 0 0 0-3 0V9l-8 5v2l8-2.5V19l-2 1.5V22l3.5-1 3.5 1v-1.5L13 19v-5.5z"/></symbol>
    <symbol id="i-doc" viewBox="0 0 24 24"><path d="M5 3h10l4 4v8M5 3v18h8" fill="none" stroke="currentColor" stroke-width="1.8"/><path d="M8 8h7M8 12h7M8 16h3" stroke="currentColor" stroke-width="1.6"/><path d="m14 21 1-3 6-6 2 2-6 6z" fill="currentColor"/></symbol>
    <symbol id="i-grid" viewBox="0 0 24 24"><g fill="currentColor"><circle cx="4" cy="4" r="2.3"/><circle cx="12" cy="4" r="2.3"/><circle cx="20" cy="4" r="2.3"/><circle cx="4" cy="12" r="2.3"/><circle cx="12" cy="12" r="2.3"/><circle cx="20" cy="12" r="2.3"/><circle cx="4" cy="20" r="2.3"/><circle cx="12" cy="20" r="2.3"/><circle cx="20" cy="20" r="2.3"/></g></symbol>
    <symbol id="i-login" viewBox="0 0 24 24"><path d="M10 3h10v18H10" fill="none" stroke="currentColor" stroke-width="2"/><path d="M2 12h12M10 8l4 4-4 4" fill="none" stroke="currentColor" stroke-width="2"/></symbol>
    <symbol id="i-account" viewBox="0 0 24 24"><circle cx="12" cy="12" r="10" fill="none" stroke="currentColor" stroke-width="2"/><circle cx="12" cy="9.5" r="3.6" fill="currentColor"/><path fill="currentColor" d="M5.5 18.5c1.5-2.5 3.8-3.6 6.5-3.6s5 1.1 6.5 3.6c-1.8 1.7-4 2.5-6.5 2.5s-4.7-.8-6.5-2.5z"/></symbol>
    <symbol id="i-calendar" viewBox="0 0 24 24"><rect x="2" y="4" width="20" height="18" rx="2" fill="currentColor"/><rect x="6" y="2" width="2" height="4" fill="currentColor"/><rect x="16" y="2" width="2" height="4" fill="currentColor"/><g fill="#fff"><rect x="5" y="10" width="3" height="3"/><rect x="10.5" y="10" width="3" height="3"/><rect x="16" y="10" width="3" height="3"/><rect x="5" y="15.5" width="3" height="3"/><rect x="10.5" y="15.5" width="3" height="3"/><rect x="16" y="15.5" width="3" height="3"/></g></symbol>
    <symbol id="i-users" viewBox="0 0 24 24"><g fill="currentColor"><circle cx="12" cy="6" r="3.5"/><circle cx="5" cy="9" r="2.6"/><circle cx="19" cy="9" r="2.6"/><path d="M6.5 21v-4.5c0-3 2.5-5 5.5-5s5.5 2 5.5 5V21z"/><path d="M0.5 21v-3.5c0-2.4 1.8-4 4.5-4 .6 0 1 .1 1.4.2C5.5 15 5 16 5 17v4z"/><path d="M23.5 21v-3.5c0-2.4-1.8-4-4.5-4-.6 0-1 .1-1.4.2.9 1.3 1.4 2.3 1.4 3.3v4z"/></g></symbol>
    <symbol id="i-dashboard" viewBox="0 0 24 24"><rect x="1.5" y="2" width="21" height="15" rx="1" fill="none" stroke="currentColor" stroke-width="1.8"/><path d="M9 21h6M12 17v4" stroke="currentColor" stroke-width="1.8"/><g fill="currentColor"><rect x="4" y="5" width="5" height="4"/><rect x="11" y="10" width="2" height="5"/><rect x="14.5" y="7" width="2" height="8"/><rect x="18" y="9" width="2" height="6"/></g></symbol>
    <symbol id="i-tracking" viewBox="0 0 24 24"><circle cx="5" cy="16" r="3.2" fill="none" stroke="currentColor" stroke-width="2"/><circle cx="18" cy="6" r="3.2" fill="none" stroke="currentColor" stroke-width="2"/><path d="M18 10.5v2.5h-5a3 3 0 0 0 0 6H22M5 19.5V22" fill="none" stroke="currentColor" stroke-width="2"/></symbol>
    <symbol id="i-event" viewBox="0 0 24 24"><rect x="2" y="4" width="20" height="18" rx="2" fill="currentColor"/><rect x="6" y="1.5" width="2" height="5" fill="currentColor"/><rect x="16" y="1.5" width="2" height="5" fill="currentColor"/><rect x="2" y="8" width="20" height="1" fill="#fff"/><path fill="#fff" d="m12 11 1.5 3 3.2.4-2.4 2.2.7 3.2L12 18.2 9 19.8l.7-3.2-2.4-2.2 3.2-.4z"/></symbol>
  </defs>
</svg>

<!-- Screen 1: More menu (handset size) -->
<section class="screen screen--phone">
  <header class="appbar">
    <h1 class="appbar__title">MORE</h1>
    <svg class="appbar__icon"><use href="#i-plus"/></svg>
    <svg class="appbar__kebab"><use href="#i-kebab"/></svg>
  </header>
  <nav class="menu">
    <div class="menu__cell"><svg><use href="#i-plane"/></svg>FLIGHT</div>
    <div class="menu__cell"><svg><use href="#i-login"/></svg>LOGIN</div>
    <div class="menu__cell"><svg><use href="#i-account"/></svg>ACCOUNT</div>
    <div class="menu__cell"><svg><use href="#i-calendar"/></svg>CALENDAR</div>
    <div class="menu__cell"><svg><use href="#i-users"/></svg>USERS</div>
    <div class="menu__cell"><svg><use href="#i-dashboard"/></svg>DASHBOARD</div>
    <div class="menu__cell"><svg><use href="#i-tracking"/></svg>TRACKING</div>
    <div class="menu__cell"><svg><use href="#i-event"/></svg>OUTREACH<br>EVENT</div>
    <div class="menu__cell"><svg><use href="#i-gear"/></svg>SETTING</div>
  </nav>
  <div class="menu__wide"><svg><use href="#i-cog"/></svg>MAINTENANCE RESOURCE</div>
  <footer class="tabbar">
    <div class="tabbar__item"><svg><use href="#i-phone"/></svg>CONTACT</div>
    <div class="tabbar__item"><svg><use href="#i-pilot"/></svg>PILOT</div>
    <div class="tabbar__item"><svg><use href="#i-plane"/></svg>PLANE</div>
    <div class="tabbar__item tabbar__item--wide"><svg><use href="#i-doc"/></svg>FLT REQUEST</div>
    <div class="tabbar__item tabbar__item--active"><svg><use href="#i-grid"/></svg>MORE</div>
  </footer>
  <div class="phone-foot"></div>
</section>

<!-- Screen 2: Pilots list -->
<section class="screen screen--pilots">
  <header class="appbar">
    <h1 class="appbar__title">PILOTS</h1>
    <svg class="appbar__icon"><use href="#i-plus"/></svg>
    <svg class="appbar__kebab"><use href="#i-kebab"/></svg>
  </header>
  <div class="search"><svg><use href="#i-search"/></svg>SEARCH</div>
  <div class="advanced"><svg><use href="#i-cog"/></svg>Advanced Search</div>
  <article class="pilot" style="top:84px">
    <div class="pilot__photo" role="img" aria-label="Pilot portrait photo"></div>
    <h2 class="pilot__name">Morgan, Ellis, Grant</h2>
    <div class="pilot__chips"><span class="chip chip--fill">3182133</span><span class="chip chip--line">9/30/24</span></div>
  </article>
  <article class="pilot" style="top:146px">
    <div class="pilot__photo" role="img" aria-label="Pilot portrait photo"></div>
    <h2 class="pilot__name">Whitfield, Daniel,</h2>
    <div class="pilot__chips"><span class="chip chip--fill">4467155</span><span class="chip chip--line">2/28/25</span></div>
  </article>
  <article class="pilot" style="top:208px">
    <div class="pilot__photo" role="img" aria-label="Pilot portrait photo"></div>
    <h2 class="pilot__name">Morgan, Ellis, Grant</h2>
    <div class="pilot__chips"><span class="chip chip--fill">3182133</span><span class="chip chip--line">9/30/24</span></div>
  </article>
  <article class="pilot" style="top:270px">
    <div class="pilot__photo" role="img" aria-label="Pilot portrait photo"></div>
    <h2 class="pilot__name">Whitfield, Daniel,</h2>
    <div class="pilot__chips"><span class="chip chip--fill">4467155</span><span class="chip chip--line">2/28/25</span></div>
  </article>
  <footer class="tabbar">
    <div class="tabbar__item"><svg><use href="#i-phone"/></svg>CONTACT</div>
    <div class="tabbar__item tabbar__item--active"><svg><use href="#i-pilot"/></svg>PILOT</div>
    <div class="tabbar__item"><svg><use href="#i-plane"/></svg>PLANE</div>
    <div class="tabbar__item tabbar__item--wide"><svg><use href="#i-doc"/></svg>FLT REQUEST</div>
    <div class="tabbar__item"><svg><use href="#i-grid"/></svg>MORE</div>
  </footer>
</section>

<!-- Screen 3: More menu -->
<section class="screen screen--more">
  <header class="appbar">
    <h1 class="appbar__title">MORE</h1>
    <svg class="appbar__icon"><use href="#i-plus"/></svg>
    <svg class="appbar__kebab"><use href="#i-kebab"/></svg>
  </header>
  <nav class="menu">
    <div class="menu__cell"><svg><use href="#i-plane"/></svg>FLIGHT</div>
    <div class="menu__cell"><svg><use href="#i-login"/></svg>LOGIN</div>
    <div class="menu__cell"><svg><use href="#i-account"/></svg>ACCOUNT</div>
    <div class="menu__cell"><svg><use href="#i-calendar"/></svg>CALENDAR</div>
    <div class="menu__cell"><svg><use href="#i-users"/></svg>USERS</div>
    <div class="menu__cell"><svg><use href="#i-dashboard"/></svg>DASHBOARD</div>
    <div class="menu__cell"><svg><use href="#i-tracking"/></svg>TRACKING</div>
    <div class="menu__cell"><svg><use href="#i-event"/></svg>OUTREACH<br>EVENT</div>
    <div class="menu__cell"><svg><use href="#i-gear"/></svg>SETTING</div>
  </nav>
  <div class="menu__wide"><svg><use href="#i-cog"/></svg>MAINTENANCE RESOURCE</div>
  <footer class="tabbar">
    <div class="tabbar__item"><svg><use href="#i-phone"/></svg>CONTACT</div>
    <div class="tabbar__item"><svg><use href="#i-pilot"/></svg>PILOT</div>
    <div class="tabbar__item"><svg><use href="#i-plane"/></svg>PLANE</div>
    <div class="tabbar__item tabbar__item--wide"><svg><use href="#i-doc"/></svg>FLT REQUEST</div>
    <div class="tabbar__item tabbar__item--active"><svg><use href="#i-grid"/></svg>MORE</div>
  </footer>
</section>

<!-- Screen 4: Contact edit -->
<section class="screen screen--contact">
  <header class="appbar">
    <svg class="appbar__icon"><use href="#i-back"/></svg>
    <h1 class="appbar__title">CONTACT</h1>
    <svg class="appbar__kebab"><use href="#i-kebab"/></svg>
  </header>
  <div class="addrow" style="top:37px">Add Email<svg><use href="#i-plus"/></svg></div>
  <div class="addrow" style="top:58.5px">Add Social Media<svg><use href="#i-plus"/></svg></div>
  <div class="addrow" style="top:80px">Add Emergency Contact<svg><use href="#i-plus"/></svg></div>
  <div class="addrow" style="top:101.5px">Add Personal Information<svg><use href="#i-plus"/></svg></div>
  <div class="addrow" style="top:123px">Add Work Info<svg><use href="#i-plus"/></svg></div>
  <div class="addrow" style="top:144.5px">Add Skills/Talents<svg><use href="#i-plus"/></svg></div>
  <div class="addrow" style="top:166px">Add Resources<svg><use href="#i-plus"/></svg></div>
  <div class="panel" style="top:194px;height:40px">
    <div class="panel__title">Pilots</div>
    <svg class="panel__toggle"><use href="#i-minus"/></svg>
    <p>Harlow, Dean, 5829301, 10/31/23</p>
  </div>
  <div class="panel" style="top:241px;height:72px">
    <div class="panel__title">Aircraft Owner</div>
    <svg class="panel__toggle"><use href="#i-minus"/></svg>
    <p>Personal: Harlow, Dean: Skyline: 40S: Skyline Aircraft Company, Single Engine, 1100</p>
    <span class="pill-btn">Add Aircraft Owner</span>
  </div>
  <footer class="tabbar">
    <div class="tabbar__item tabbar__item--active"><svg><use href="#i-phone"/></svg>CONTACT</div>
    <div class="tabbar__item"><svg><use href="#i-pilot"/></svg>PILOT</div>
    <div class="tabbar__item"><svg><use href="#i-plane"/></svg>PLANE</div>
    <div class="tabbar__item tabbar__item--wide"><svg><use href="#i-doc"/></svg>FLT REQUEST</div>
    <div class="tabbar__item"><svg><use href="#i-grid"/></svg>MORE</div>
  </footer>
</section>

<!-- Screen 5: Work order detail -->
<section class="screen screen--workorder">
  <header class="appbar">
    <svg class="appbar__icon"><use href="#i-back"/></svg>
    <h1 class="appbar__title">WORK ORDER</h1>
    <svg class="appbar__kebab"><use href="#i-kebab"/></svg>
  </header>
  <div class="toggle-row">
    <span class="toggle" style="width:49px">Extra Soft</span>
    <span class="toggle" style="width:33px">Soft</span>
    <span class="toggle toggle--on" style="width:36px">Medium</span>
    <span class="toggle" style="width:36px">Hard</span>
  </div>
  <div class="action-row">
    <span class="action" style="width:44px"><svg><use href="#i-doc"/></svg>Print</span>
    <span class="action" style="width:45px"><svg><use href="#i-doc"/></svg>Create</span>
  </div>
  <dl class="detail">
    <svg class="detail__toggle"><use href="#i-minus"/></svg>
    <div class="field"><dt>Customer</dt><dd>Rahman, Samir</dd></div>
    <div class="field"><dt>Service Location</dt><dd>Billing, 418 Willow Crest Lane, Denton, TX, 76201</dd></div>
    <div class="field"><dt>Billing Address</dt><dd>Billing, 418 Willow Crest Lane, Denton, TX, 76201</dd></div>
    <div class="field"><dt>Description</dt><dd>Pool maintenance</dd></div>
    <div class="field"><dt>Work Order Type</dt><dd>One off job</dd></div>
    <div class="field"><dt>WO Status</dt><dd>Active</dd></div>
    <div class="field"><dt>Billing Frequency</dt><dd>Upon job completion</dd></div>
  </dl>
  <div class="addrow" style="top:290px;left:8.5px">Add Technician<svg><use href="#i-plus"/></svg></div>
  <div class="addrow" style="top:312px;left:8.5px">Add Line Items<svg><use href="#i-plus"/></svg></div>
  <footer class="tabbar">
    <div class="tabbar__item"><svg><use href="#i-phone"/></svg>CONTACT</div>
    <div class="tabbar__item"><svg><use href="#i-pilot"/></svg>PILOT</div>
    <div class="tabbar__item"><svg><use href="#i-plane"/></svg>PLANE</div>
    <div class="tabbar__item tabbar__item--wide"><svg><use href="#i-doc"/></svg>FLT REQUEST</div>
    <div class="tabbar__item"><svg><use href="#i-grid"/></svg>MORE</div>
  </footer>
</section>
</body>
</html>
```